Dental specialist needs a sharp looking letterhead

I am looking for a letterhead to be used to send letters and communication between myself (a dental specialist) and other dentists.
My office is a state of the art dental specialty office.
I need to letterhead to also state:
Bertram L. Oswick DDS
2748 Tollard Avenue, Suite K
West Tollard, NY 14391
(716)392-5061
fax: (716)392-5087
oswickroot.com (**this email address may change)

i included my logo designs.
thank you

Target Market(s)

dentists

Industry/Entity Type

Communication

Requirements
Must have
• the included logo, whether the vertical or horizontal versions

```html
<!DOCTYPE html>
<html lang="en">
<head>
<meta charset="utf-8">
<title>Meridian Endodontics P.C. — Letterhead</title>
<link href="https://fonts.googleapis.com/css2?family=Roboto+Slab:wght@300;400&display=swap" rel="stylesheet">
<style>
  :root {
    --sky: #45a5dc;
    --leaf: #8cc63f;
    --ink: #141414;
    --text: #333333;
    --paper: #ffffff;
  }
  html, body {
    margin: 0;
    padding: 0;
    width: 931px;
    height: 1200px;
    overflow: hidden;
    background: var(--paper);
  }
  .letterhead {
    position: relative;
    width: 931px;
    height: 1200px;
    background: var(--paper);
    font-family: "Roboto Slab", Georgia, serif;
    font-weight: 300;
    color: var(--text);
  }
  .header-waves {
    position: absolute;
    top: 0;
    left: 0;
    width: 931px;
    height: 270px;
  }
  .brand {
    position: absolute;
    top: 118px;
    left: 86px;
    display: flex;
    align-items: center;
    gap: 14px;
    color: var(--ink);
    font-weight: 400;
  }
  .brand-dot {
    width: 44px;
    height: 44px;
    border-radius: 50%;
    background: var(--ink);
  }
  .brand-name {
    display: flex;
    flex-direction: column;
    align-items: center;
    border-left: 1px solid var(--ink);
    padding-left: 8px;
  }
  .brand-name .primary {
    font-size: 38px;
    line-height: 1;
    letter-spacing: -0.5px;
  }
  .brand-name .secondary {
    font-size: 14px;
    letter-spacing: 2px;
    margin-top: 2px;
  }
  .doctor {
    position: absolute;
    top: 16px;
    left: 560px;
    width: 290px;
    text-align: center;
    color: var(--paper);
  }
  .doctor .name {
    font-size: 20px;
    line-height: 1;
  }
  .doctor .phone {
    margin-top: 12px;
    font-size: 15px;
    display: flex;
    justify-content: center;
    align-items: center;
    gap: 7px;
  }
  .contact {
    position: absolute;
    top: 108px;
    right: 30px;
    width: 460px;
    text-align: right;
    font-size: 15px;
  }
  .contact .line {
    display: flex;
    justify-content: center;
    align-items: center;
    gap: 8px;
    height: 25px;
    padding-left: 120px;
  }
  .contact .address {
    margin-top: 2px;
    font-size: 16.5px;
    letter-spacing: -0.3px;
  }
  .icon { display: block; }
</style>
</head>
<body>
  <main class="letterhead">
    <svg class="header-waves" viewBox="0 0 931 270" aria-hidden="true">
      <path fill="var(--sky)" d="M0,0 H931 C850,60 780,85 690,85 C560,85 420,40 300,42 C150,44 40,100 0,175 Z"/>
      <path fill="var(--leaf)" d="M931,0 C860,72 780,104 680,102 C540,99 380,56 250,56 C175,57 110,80 55,125 C110,68 200,42 300,42 C420,40 560,85 690,85 C780,85 850,60 931,0 Z"/>
      <path fill="var(--ink)" d="M434,90 C300,70 150,70 70,128 C30,158 8,205 0,262 L0,232 C10,188 35,143 75,116 C155,64 300,66 434,90 Z"/>
    </svg>

    <div class="brand">
      <span class="brand-dot"></span>
      <div class="brand-name">
        <span class="primary">MERIDIAN</span>
        <span class="secondary">Endodontics P.C.</span>
      </div>
    </div>

    <div class="doctor">
      <div class="name">Bertram L. Oswick, DDS</div>
      <div class="phone">
        <svg class="icon" width="14" height="14" viewBox="0 0 14 14" aria-hidden="true">
          <circle cx="7" cy="7" r="6" fill="none" stroke="#fff" stroke-width="1.2"/>
          <path d="M5,3.8 C4,5 4.3,8 6.8,10 L8.2,9 L7.4,7.9 L6.8,8.2 C6,7.3 5.8,6.3 6,5.6 L6.6,5.4 L6.3,4 Z" fill="#fff"/>
        </svg>
        <span>716-392-5061</span>
      </div>
    </div>

    <div class="contact">
      <div class="line">
        <svg class="icon" width="16" height="13" viewBox="0 0 16 13" aria-hidden="true">
          <rect x="3" y="0" width="10" height="4" fill="var(--leaf)"/>
          <rect x="0" y="4" width="16" height="7" rx="2" fill="var(--leaf)"/>
          <rect x="4" y="8" width="8" height="5" fill="var(--leaf)" stroke="#fff" stroke-width="1"/>
        </svg>
        <span>716-392-5087</span>
      </div>
      <div class="line">
        <svg class="icon" width="16" height="11" viewBox="0 0 16 11" aria-hidden="true">
          <rect x="0" y="0" width="16" height="11" fill="var(--sky)"/>
          <path d="M0,0 L8,6 L16,0" fill="none" stroke="#fff" stroke-width="1.2"/>
        </svg>
        <span>oswickroot@gmail.com</span>
      </div>
      <div class="address">2748 Tollard Avenue, Suite K, West Tollard, NY 14391</div>
    </div>
  </main>
</body>
</html>
```